Vorn upkeep KT Solar Venture

Solar power system install
Services and maintenance
wiring, Rewinding and Renovation
Switch Board Upgrade
Power and lighting point
t doesn’t matter how much you spend on quality parts, your solar system will let you down if your design and installation are sub-par. Have your solar system tailored and installed by our Master Electrician and Bright Grid Guild Accredited team.

Target Market(s)

sales and installed

Industry/Entity Type

Solar install and retailer

Contact Information for Business Card

Name , Email, Phone Number ,Business address,

Font styles to use
Serif

Colors
0054AA
0677BA
7BADD7
CADEEF
E8F1F8

Requirements
Must have
• clear and bright
Nice to have
• new design
Should not have
• unclear pictures

```html
<!DOCTYPE html>
<html lang="en">
<head>
<meta charset="utf-8">
<title>Vorn upkeep – KT Solar Venture business card</title>
<link href="https://fonts.googleapis.com/css2?family=Roboto:wght@300;400;500;700&display=swap" rel="stylesheet">
<style>
  :root {
    --bg: #2c2c2c;
    --card: #f3f3f3;
    --card-edge: #e6e6e6;
    --blue-deep: #0054AA;
    --blue: #0677BA;
    --green: #2e9a3a;
    --green-light: #6aa83a;
    --ink: #1c1c1c;
    --white: #ffffff;
  }
  * { margin: 0; padding: 0; box-sizing: border-box; }
  html, body { width: 1200px; height: 1138px; overflow: hidden; }
  body {
    background: var(--bg);
    font-family: "Roboto", Arial, sans-serif;
    position: relative;
  }
  .card {
    position: absolute;
    border-radius: 14px;
    background: linear-gradient(180deg, var(--white) 0%, var(--card) 60%, var(--card-edge) 100%);
    overflow: hidden;
  }
  .card--front { left: 274px; top: 186px; width: 623px; height: 376px; }
  .card--back  { left: 275px; top: 607px; width: 619px; height: 375px; }

  .brand-dot {
    position: absolute;
    border-radius: 50%;
    background: var(--blue);
  }
  .brand-name {
    position: absolute;
    color: var(--blue-deep);
    font-weight: 700;
    text-transform: uppercase;
    line-height: 1.02;
    letter-spacing: 0.5px;
  }

  /* front */
  .card--front .brand-dot { left: 128px; top: 86px; width: 72px; height: 72px; }
  .card--front .brand-name { left: 238px; top: 110px; font-size: 31px; }

  .services-band {
    position: absolute;
    left: 0; top: 239px; width: 100%; height: 74px;
    background: linear-gradient(90deg, var(--green-light) 0%, #3f9a6a 40%, var(--blue) 70%, var(--blue) 100%);
    color: var(--white);
    font-weight: 300;
    font-size: 15.5px;
    text-align: center;
    padding-top: 13px;
    line-height: 23px;
  }
  .services-band .sep { margin: 0 6px; }

  .web-row {
    position: absolute;
    left: 0; top: 332px; width: 100%;
    text-align: center;
    font-size: 15.5px;
    color: var(--ink);
  }
  .rule {
    position: absolute;
    top: 342px; height: 2px; width: 80px;
  }
  .rule--left { left: 112px; background: linear-gradient(90deg, transparent, var(--blue)); }
  .rule--right { left: 431px; background: linear-gradient(90deg, var(--green), transparent); }

  /* back */
  .wave { position: absolute; left: 0; top: 0; width: 100%; height: 100%; }
  .person {
    position: absolute; right: 29px; top: 30px; text-align: right; color: var(--white);
  }
  .person__name { font-size: 24px; font-weight: 500; line-height: 30px; }
  .person__role { font-size: 15.5px; font-weight: 400; margin-top: 2px; }

  .card--back .brand-dot { left: 125px; top: 135px; width: 80px; height: 80px; }
  .card--back .brand-name { left: 30px; top: 268px; font-size: 33px; }

  .address {
    position: absolute; right: 29px; top: 212px;
    text-align: right; font-size: 16px; line-height: 23.5px; color: var(--ink);
  }
  .contacts {
    position: absolute; right: 29px; top: 265px;
    list-style: none; font-size: 16px; color: var(--ink);
  }
  .contacts li {
    display: flex; align-items: center; justify-content: flex-end;
    height: 24px;
  }
  .contacts svg { width: 14px; height: 14px; margin-left: 12px; fill: var(--green); }
</style>
</head>
<body>

<section class="card card--front">
  <span class="brand-dot"></span>
  <div class="brand-name">Vorn upkeep<br>KT Solar Venture</div>

  <div class="services-band">
    <div>Solar Power System Install<span class="sep">|</span>Wiring, Rewinding &amp; Renovation</div>
    <div>Services &amp; Maintenance<span class="sep">|</span>Switch Board Upgrade<span class="sep">|</span>Power &amp; Lighting Point</div>
  </div>

  <span class="rule rule--left"></span>
  <div class="web-row">www.ktsolarventure.com</div>
  <span class="rule rule--right"></span>
</section>

<section class="card card--back">
  <svg class="wave" viewBox="0 0 774 469" preserveAspectRatio="none" aria-hidden="true">
    <path d="M0,0 H774 V142 C660,170 560,120 440,70 C320,20 150,10 0,40 Z" fill="#0677BA"/>
    <path d="M0,78 C150,25 300,25 430,72 C560,125 660,185 774,152" fill="none" stroke="#2e9a3a" stroke-width="9"/>
    <path d="M60,70 C170,40 290,45 380,65" fill="none" stroke="#2e9a3a" stroke-width="4" opacity="0.8"/>
  </svg>

  <div class="person">
    <div class="person__name">John Doe Smith</div>
    <div class="person__role">Managing Director</div>
  </div>

  <span class="brand-dot"></span>
  <div class="brand-name">Vorn upkeep<br>KT Solar Venture</div>

  <div class="address">234 Anywhere St., Any City,<br>Any Town, US 123456</div>

  <ul class="contacts">
    <li>828-111-1111
      <svg viewBox="0 0 16 16"><path d="M3 1h3l1 4-2 1c1 2 3 4 5 5l1-2 4 1v3c0 1-1 2-2 2C7 15 1 9 1 3c0-1 1-2 2-2z"/></svg>
    </li>
    <li>john@yourwebsite.com
      <svg viewBox="0 0 16 16"><path d="M1 3h14v10H1z M2 4l6 5 6-5" fill="#2e9a3a"/><path d="M2 4l6 5 6-5" fill="none" stroke="#fff" stroke-width="1.3"/></svg>
    </li>
    <li>www.yourwebsite.com
      <svg viewBox="0 0 16 16"><circle cx="8" cy="8" r="7"/><path d="M1 8h14M8 1c-3 3-3 11 0 14M8 1c3 3 3 11 0 14M2.5 4.5h11M2.5 11.5h11" fill="none" stroke="#fff" stroke-width="1"/></svg>
    </li>
  </ul>
</section>

</body>
</html>
```